Lumavento business card

We need a modern business card - With our 4 colors - See web: www.lumavento.dk

I have attached logo and som old business Cards we have - Lets Make the new ones shine...:-) -

Industry/Entity Type

Business

Requirements
Must have
• the logo with lumavento only,

```html
<!DOCTYPE html>
<html lang="da">
<head>
<meta charset="utf-8">
<title>Lumavento – visitkort</title>
<link href="https://fonts.googleapis.com/css2?family=Mulish:wght@400;700&display=swap" rel="stylesheet">
<style>
  :root {
    --backdrop: #d9d9d9;
    --card: #ffffff;
    --lime: #8dc63f;
    --ink: #2a2a2a;
    --grey: #6a6a6a;
    --night: #000000;
  }
  * { margin: 0; padding: 0; box-sizing: border-box; }
  html, body {
    width: 1105px; height: 1200px; overflow: hidden;
    background: var(--backdrop);
    font-family: "Mulish", Arial, sans-serif;
  }
  .card {
    position: absolute; left: 102px;
    width: 901px; height: 515px;
    background: var(--card);
    border-radius: 30px;
    overflow: hidden;
  }
  .card--front { top: 35px; }
  .card--back { top: 650px; }
  .card__art { position: absolute; inset: 0; }

  .wordmark {
    position: absolute; left: 43px; top: 30px;
    font-size: 50px; font-weight: 400; letter-spacing: 4px;
    color: var(--ink);
  }
  .person { position: absolute; left: 43px; top: 148px; }
  .person__name { font-size: 34px; font-weight: 700; color: var(--lime); line-height: 1.1; }
  .person__role { font-size: 25px; color: var(--ink); line-height: 1.2; }

  .address {
    position: absolute; left: 45px; top: 246px;
    font-size: 26px; line-height: 36px; color: var(--grey); font-style: normal;
  }
  .contacts { position: absolute; left: 45px; top: 328px; list-style: none; }
  .contacts li {
    display: flex; align-items: center; gap: 16px;
    height: 37.5px; font-size: 26px; color: var(--grey);
  }
  .contacts svg { width: 22px; height: 22px; fill: var(--lime); flex: none; }

  .back__brand {
    position: absolute; left: 0; right: 0; top: 150px;
    display: flex; flex-direction: column; align-items: center;
  }
  .back__mark { width: 110px; height: 110px; }
  .back__name {
    margin-top: 28px; font-size: 32px; letter-spacing: 3px; color: var(--ink);
    line-height: 40px;
  }
  .back__rule {
    width: 368px; height: 3px; background: var(--lime); margin-top: 12px;
  }
  .back__tagline { margin-top: 22px; font-size: 22px; color: var(--ink); }
</style>
</head>
<body>

<section class="card card--front">
  <svg class="card__art" viewBox="0 0 901 515" aria-hidden="true">
    <path d="M830 0 H901 V515 H690 Q860 330 830 0 Z" fill="var(--night)"/>
  </svg>

  <div class="wordmark">lumavento</div>

  <div class="person">
    <div class="person__name">Mikkel Havgaard</div>
    <div class="person__role">Salgsdirektør</div>
  </div>

  <address class="address">Solsikkevej 14<br>2100 Nordhavn</address>

  <ul class="contacts">
    <li><svg viewBox="0 0 24 24"><path d="M6.6 10.8a15.1 15.1 0 0 0 6.6 6.6l2.2-2.2c.3-.3.7-.4 1-.2 1.1.4 2.3.6 3.6.6.6 0 1 .4 1 1V20c0 .6-.4 1-1 1C10.6 21 3 13.4 3 4c0-.6.4-1 1-1h3.5c.6 0 1 .4 1 1 0 1.3.2 2.5.6 3.6.1.3 0 .7-.2 1l-2.3 2.2z"/></svg>+45 31 20 40 60</li>
    <li><svg viewBox="0 0 24 24"><path d="M6.6 10.8a15.1 15.1 0 0 0 6.6 6.6l2.2-2.2c.3-.3.7-.4 1-.2 1.1.4 2.3.6 3.6.6.6 0 1 .4 1 1V20c0 .6-.4 1-1 1C10.6 21 3 13.4 3 4c0-.6.4-1 1-1h3.5c.6 0 1 .4 1 1 0 1.3.2 2.5.6 3.6.1.3 0 .7-.2 1l-2.3 2.2z"/></svg>+45 52 70 80 90</li>
    <li><svg viewBox="0 0 24 24"><path d="M2 5h20v14H2z"/><path d="M3 6l9 7 9-7" fill="none" stroke="#fff" stroke-width="1.6"/></svg>mh@lumavento.dk</li>
    <li><svg viewBox="0 0 24 24"><circle cx="12" cy="12" r="10"/><path d="M7 8c2 0 3 1 3 3s-2 2-2 4M14 5c0 2 2 3 4 3M15 14c1 1 1 3 0 5" fill="none" stroke="#fff" stroke-width="1.5"/></svg>www.lumavento.dk</li>
  </ul>
</section>

<section class="card card--back">
  <div class="back__brand">
    <svg class="back__mark" viewBox="0 0 90 90" aria-hidden="true">
      <circle cx="45" cy="45" r="40" fill="none" stroke="var(--lime)" stroke-width="5"/>
    </svg>
    <div class="back__name">lumavento</div>
    <div class="back__rule"></div>
    <div class="back__tagline">idéer der lyser</div>
  </div>
</section>

</body>
</html>
```